Card Design for my dog training business Brightpaw Obedience

Need a business card design for my dog training business with my new logo. Want the card to come off professional yet fun. Want it to be very eye catchy as well. I normally have these at vet clinics, pet stores, and groomers. so need it to look better than my competitors.
Target Market(s)
dog owners
Industry/Entity Type
Dog Training
Contact Information for Business Card
needs logo, my name and info
Font styles to use
Serif
Colors
0255a3
ffffff
ec1f27
000000
333333
fbfbfb
Requirements
Must have
- Brightpaw Obedience
- Felix Orland
- 415 903 2276
- info@brightpawobedience.example
- www.brightpawobedience.example

```html
<!DOCTYPE html>
<html lang="en">
<head>
<meta charset="utf-8">
<title>Brightpaw Obedience – Business Card</title>
<link rel="stylesheet" href="https://fonts.googleapis.com/css2?family=EB+Garamond:ital,wght@0,400;1,400&family=Lato:wght@400&family=Tinos&display=swap">
<style>
  :root {
    --page-bg: #d8d2cb;
    --card-top: #3d3735;
    --card-bottom: #2b2625;
    --accent-red: #c9262c;
    --text-light: #d9d4ce;
    --logo-cream: #e9dfc8;
    --tagline: #cdbfa6;
  }
  * { margin: 0; padding: 0; box-sizing: border-box; }
  html, body {
    width: 1200px;
    height: 1047px;
    overflow: hidden;
    background: var(--page-bg);
  }
  .business-card {
    position: absolute;
    left: 100px;
    top: 251px;
    width: 1000px;
    height: 545px;
    border-radius: 24px;
    background: linear-gradient(160deg, var(--card-top), var(--card-bottom));
    box-shadow: 0 18px 40px rgba(0,0,0,0.25);
    overflow: hidden;
  }
  .contact-side {
    position: absolute;
    left: 50px;
    top: 0;
    width: 420px;
    height: 100%;
    font-family: "Lato", sans-serif;
    color: var(--text-light);
  }
  .person-name {
    position: absolute;
    top: 48px;
    font-family: "Tinos", "Times New Roman", serif;
    font-size: 24px;
    letter-spacing: 0.5px;
    color: var(--accent-red);
    text-transform: uppercase;
    font-weight: 400;
  }
  .person-title {
    position: absolute;
    top: 84px;
    font-size: 21px;
  }
  .address {
    position: absolute;
    top: 230px;
    font-size: 21px;
    line-height: 36px;
    font-style: normal;
  }
  .contact-list {
    position: absolute;
    top: 393px;
    list-style: none;
    font-size: 21px;
    line-height: 35px;
  }
  .contact-list li {
    display: flex;
    align-items: center;
    gap: 10px;
  }
  .contact-icon {
    width: 14px;
    height: 14px;
    flex: none;
  }
  .brand-side {
    position: absolute;
    left: 480px;
    top: 0;
    width: 520px;
    height: 100%;
    text-align: center;
  }
  .brand-name {
    position: absolute;
    left: 0;
    right: 0;
    top: 170px;
    font-family: "EB Garamond", serif;
    font-weight: 400;
    font-size: 60px;
    line-height: 66px;
    color: var(--logo-cream);
  }
  .tagline {
    position: absolute;
    left: 0;
    right: 0;
    top: 465px;
    font-family: "EB Garamond", serif;
    font-style: italic;
    font-size: 20px;
    color: var(--tagline);
  }
</style>
</head>
<body>
  <main class="business-card">
    <section class="contact-side">
      <h1 class="person-name">Felix Orland</h1>
      <p class="person-title">Managing Director</p>
      <address class="address">218 Larkspur Lane,<br>Ashford, NZ, 8042</address>
      <ul class="contact-list">
        <li>
          <svg class="contact-icon" viewBox="0 0 14 14" aria-hidden="true"><path fill="#c9262c" d="M3 1l2.5 3-1.4 1.6c.8 1.7 2.2 3.1 3.9 3.9L9.6 8 13 10.5 11.6 13C6 12.6 1.4 8 1 2.4z"/></svg>
          <span>415 903 2276</span>
        </li>
        <li>
          <svg class="contact-icon" viewBox="0 0 14 14" aria-hidden="true"><rect x="1" y="3" width="12" height="8.5" rx="1" fill="none" stroke="#c9262c" stroke-width="1.6"/><path d="M1.5 3.8L7 8l5.5-4.2" fill="none" stroke="#c9262c" stroke-width="1.6"/></svg>
          <span>info@brightpawobedience.example</span>
        </li>
        <li>
          <svg class="contact-icon" viewBox="0 0 14 14" aria-hidden="true"><circle cx="7" cy="7" r="5.8" fill="none" stroke="#c9262c" stroke-width="1.6"/><path d="M1.5 7h11M7 1.2c-2.6 3.4-2.6 8.2 0 11.6M7 1.2c2.6 3.4 2.6 8.2 0 11.6" fill="none" stroke="#c9262c" stroke-width="1.2"/></svg>
          <span>www.brightpawobedience.example</span>
        </li>
      </ul>
    </section>
    <section class="brand-side">
      <p class="brand-name">Brightpaw<br>Obedience</p>
      <p class="tagline">“Training dogs across Texas one dog at a time.”</p>
    </section>
  </main>
</body>
</html>
```